Calverbrook.com.au - Pelvane Australia - Uncoded PSD only

We need a web design for a virtual assistant company based in Sydney Australia called "Calverbrook". We provide virtual assistance and unlimited admin tasks to small business owners for a monthly fee. We would like to see designs that are not too different to www.pelvane.com. Words to describe the design and feel of this website are sleek and professional. We want to use bright inviting colours for the call to action buttons and a professional business focused background.

Target Market(s)

business executives, business owners, small business owners, those professionals who lack time.

Industry/Entity Type

Business Consultant

Number of Pages Required

3 page

Font styles to use
Sans Serif

Colors
5e5e5e
1b1b1b
3176b5
33b8a4

Requirements
Must have
• Call to action buttons, sleek business feel think snorbix.io and pelvane.com
Nice to have
• Bold back ground colours, bright call to action buttons
Should not have
• too much white

```html
<!DOCTYPE html>
<html lang="en">
<head>
<meta charset="utf-8">
<title>Calverbrook – Virtual Assistance</title>
<link href="https://fonts.googleapis.com/css2?family=Raleway:wght@300;400;500;600;700&family=Open+Sans:wght@400;600&display=swap" rel="stylesheet">
<style>
:root{
  --teal:#33b8a4;
  --blue:#3176b5;
  --ink:#1b1b1b;
  --grey:#5e5e5e;
  --dark:#232323;
  --footer:#1c2a3a;
  --white:#ffffff;
  --light:#f4f4f4;
}
*{margin:0;padding:0;box-sizing:border-box}
html,body{width:1200px;height:2596px;overflow:hidden}
body{font-family:'Open Sans',Arial,sans-serif;color:var(--grey);background:var(--white);position:relative}
h1,h2,h3,h4,.logo,.nav{font-family:'Raleway',Arial,sans-serif}
.wrap{width:870px;margin:0 auto;position:relative}
.btn{display:inline-block;font-family:'Raleway',Arial,sans-serif;font-size:13px;letter-spacing:1px;text-transform:uppercase;padding:8px 20px;border:2px solid var(--white);color:var(--white);text-decoration:none}
.btn-solid{background:var(--teal);border-color:var(--teal);text-transform:none;font-size:15px;padding:10px 30px;letter-spacing:0}
.btn-outline-blue{border:1px solid var(--blue);color:var(--blue);font-size:12px;padding:7px 16px}

/* Hero */
.hero{position:absolute;top:0;left:0;width:1200px;height:612px;overflow:hidden}
.hero-photo{position:absolute;inset:0;background:linear-gradient(100deg,#6f8390 0%,#8ea0a9 30%,#5e6e78 60%,#3b4a54 100%)}
.hero-shade{position:absolute;inset:0;background:rgba(20,30,40,.35)}
.nav{position:absolute;top:0;left:0;right:0;height:66px;background:rgba(20,30,40,.35)}
.nav .wrap{display:flex;align-items:center;height:66px}
.logo{color:var(--white);font-size:24px;font-weight:500}
.menu{margin-left:auto;display:flex;gap:26px;font-size:11px;font-weight:600;color:var(--white);text-transform:uppercase;letter-spacing:.5px}
.phone{margin-left:26px;display:flex;align-items:center;gap:8px;color:var(--white);font-size:15px;font-weight:600}
.hero-text{position:absolute;top:250px;left:0;right:0;text-align:center;color:var(--white)}
.hero-text h1{font-weight:400;font-size:44px}
.hero-text h2{font-weight:400;font-size:26px;color:var(--teal);margin-top:6px}
.hero-text p{font-size:12px;width:520px;margin:14px auto 0;line-height:1.5}
.hero-text .btn{margin-top:22px}
.dots{position:absolute;bottom:20px;left:0;right:0;display:flex;justify-content:center;gap:8px}
.dots span{width:10px;height:10px;border-radius:50%;background:rgba(255,255,255,.55)}
.dots span:first-child{background:var(--white)}

/* Services */
.services{position:absolute;top:612px;left:0;width:1200px;height:368px;background:var(--white)}
.services .wrap{display:flex;justify-content:space-between;padding-top:88px}
.service{width:250px;text-align:center}
.service h3{font-weight:400;font-size:24px;color:var(--ink);margin-top:6px}
.service p{font-size:11px;line-height:1.6;margin:10px 0 18px}

/* What we do */
.whatwedo{position:absolute;top:980px;left:0;width:1200px;height:370px;background:var(--teal);color:var(--white)}
.whatwedo .wrap{display:flex;padding-top:78px}
.whatwedo .copy{width:470px}
.whatwedo h2{font-weight:400;font-size:30px}
.whatwedo p{font-size:11px;line-height:1.6;margin-top:12px}
.whatwedo .btn{margin-top:22px;font-size:11px}
.video{margin-left:auto;margin-top:10px;width:270px;height:140px;position:relative;background:linear-gradient(135deg,#dfe4e8,#aab5bd)}
.video svg{position:absolute;left:50%;top:50%;transform:translate(-50%,-50%)}

/* Testimonials */
.clients{position:absolute;top:1350px;left:0;width:1200px;height:370px;background:var(--ink)}
.clients h2{text-align:center;color:var(--white);font-weight:400;font-size:26px;padding-top:74px}
.cards{display:flex;justify-content:space-between;margin-top:30px}
.card{width:270px;text-align:center}
.card blockquote{background:var(--white);color:var(--grey);font-size:10px;line-height:1.6;padding:14px 16px;height:104px}
.avatar{width:44px;height:44px;border-radius:50%;margin:14px auto 6px;background:linear-gradient(135deg,#e0b08e,#9a6a4d)}
.card h4{color:var(--white);font-weight:400;font-size:14px}
.card span{color:#8a8a8a;font-size:10px}

/* How we work */
.howwework{position:absolute;top:1720px;left:0;width:1200px;height:360px;background:var(--white)}
.woman{position:absolute;left:200px;top:10px;width:250px;height:350px;background:linear-gradient(180deg,#efe6d9 0%,#d7b98c 25%,#cfe0ee 55%,#a9c6e2 100%);border-radius:120px 120px 0 0}
.howwework .copy{position:absolute;left:565px;top:72px;width:470px}
.howwework h2{font-weight:400;font-size:30px;color:var(--grey)}
.howwework p{font-size:11px;line-height:1.6;margin-top:12px}
.howwework .btn{margin-top:18px;font-size:11px;padding:6px 14px;text-transform:uppercase}

/* Consultation */
.consult{position:absolute;top:2080px;left:0;width:1200px;height:250px;background:linear-gradient(180deg,#3176b5 0%,#2a66a0 70%,#1f4f80 100%);text-align:center;color:var(--white)}
.consult h2{font-weight:400;font-size:34px;padding-top:52px}
.consult p{font-size:15px;margin-top:8px;color:#dbe8f5}
.consult .btn{margin-top:22px;text-transform:none;font-size:15px;padding:8px 26px}

/* Footer */
.footer{position:absolute;top:2330px;left:0;width:1200px;height:266px;background:var(--footer);color:#b8c2cc}
.cols{display:flex;padding-top:42px;font-size:11px}
.col h4{color:var(--white);font-size:12px;font-weight:600;text-transform:uppercase;margin-bottom:10px}
.col li{list-style:none;line-height:1.65}
.col:nth-child(1){width:170px}
.col:nth-child(2){width:155px}
.col:nth-child(3){width:190px}
.social{display:flex;gap:10px;margin-top:10px}
.social span{width:18px;height:18px;border-radius:50%;background:#6e8aa5}
.copyright{position:absolute;left:165px;bottom:18px;font-size:10px;color:#7d8a97}
</style>
</head>
<body>

<header class="hero">
  <div class="hero-photo" role="img" aria-label="Photo of a smiling businessman in a bright modern office"></div>
  <div class="hero-shade"></div>
  <nav class="nav">
    <div class="wrap">
      <div class="logo">Calverbrook</div>
      <div class="menu"><span>About Us</span><span>Services</span><span>What We Do</span><span>Support</span></div>
      <div class="phone">
        <svg width="18" height="18" viewBox="0 0 24 24"><circle cx="12" cy="12" r="12" fill="#33b8a4"/><path d="M8 6l2 3-1 1.5c.8 1.8 2.2 3.2 4 4l1.5-1 3 2-1 2c-5 0-10-5-10-10z" fill="#fff"/></svg>
        (02) 5550 0184
      </div>
    </div>
  </nav>
  <div class="hero-text">
    <h1>Maecenas aliquet velit velturpis</h1>
    <h2>Donec quis magna hendrerit accumsan</h2>
    <p>Reliable virtual assistants who handle your admin so you can focus on growing your business. Flexible support, one simple monthly fee, no long contracts and no hidden costs at all.</p>
    <a class="btn btn-solid">Learn More</a>
  </div>
  <div class="dots"><span></span><span></span><span></span><span></span></div>
</header>

<section class="services">
  <div class="wrap">
    <div class="service">
      <svg width="40" height="36" viewBox="0 0 40 36"><rect x="13" y="2" width="14" height="8" rx="2" fill="none" stroke="#3176b5" stroke-width="3"/><rect x="2" y="9" width="36" height="25" rx="3" fill="#3176b5"/><rect x="17" y="19" width="6" height="5" fill="#fff"/></svg>
      <h3>Virtual Assistance</h3>
      <p>Dedicated assistants manage your inbox, calendar and calls so every day runs smoothly and no client request ever slips through.</p>
      <a class="btn btn-outline-blue">Click Here</a>
    </div>
    <div class="service">
      <svg width="40" height="36" viewBox="0 0 40 36"><rect x="2" y="2" width="36" height="24" rx="2" fill="none" stroke="#3176b5" stroke-width="3"/><rect x="16" y="26" width="8" height="5" fill="#3176b5"/><rect x="10" y="31" width="20" height="3" fill="#3176b5"/></svg>
      <h3>Admin Tasks</h3>
      <p>Unlimited data entry, invoicing, bookings and reports handled quickly and accurately by our trained Sydney based team members.</p>
      <a class="btn btn-outline-blue">Click Here</a>
    </div>
    <div class="service">
      <svg width="40" height="36" viewBox="0 0 40 36"><path d="M30 2a8 8 0 0 0-7.5 10.5L6 29l3 3 16.5-16.5A8 8 0 0 0 36 8l-5 3-4-2-1-4z" fill="#3176b5"/></svg>
      <h3>Business Support</h3>
      <p>Practical help with research, customer service and planning, giving busy owners the extra hands they need to grow with ease.</p>
      <a class="btn btn-outline-blue">Click Here</a>
    </div>
  </div>
</section>

<section class="whatwedo">
  <div class="wrap">
    <div class="copy">
      <h2>What We Do</h2>
      <p>We take care of the daily admin that keeps your business moving. From emails and scheduling to bookkeeping and research, our assistants become part of your team and work the way you do, every single day.</p>
      <p>Simply tell us what needs doing and we get it done fast. One monthly fee covers unlimited tasks with friendly local support.</p>
      <a class="btn">Learn More</a>
    </div>
    <div class="video" role="img" aria-label="Video still of a businessman working at his desk">
      <svg width="34" height="34" viewBox="0 0 34 34"><circle cx="17" cy="17" r="17" fill="#1b1b1b"/><path d="M13 10l11 7-11 7z" fill="#fff"/></svg>
    </div>
  </div>
</section>

<section class="clients">
  <div class="wrap">
    <h2>What Our Client Says</h2>
    <div class="cards">
      <div class="card">
        <blockquote>Working with this team has given me back hours every week. Everything is handled promptly and professionally, and I can finally focus on my clients instead of paperwork. Highly recommended.</blockquote>
        <div class="avatar" role="img" aria-label="Client portrait"></div>
        <h4>By Author Name</h4><span>Job Position</span>
      </div>
      <div class="card">
        <blockquote>Our admin used to pile up at the end of each month. Now it is done on time, every time, and the monthly fee is far less than hiring. A simple and smart choice for any small business.</blockquote>
        <div class="avatar" role="img" aria-label="Client portrait"></div>
        <h4>By Author Name</h4><span>Job Position</span>
      </div>
      <div class="card">
        <blockquote>Friendly, reliable and always quick to respond. My assistant understands how my business runs and takes care of the details so I never have to worry about them again. Great service.</blockquote>
        <div class="avatar" role="img" aria-label="Client portrait"></div>
        <h4>By Author Name</h4><span>Job Position</span>
      </div>
    </div>
  </div>
</section>

<section class="howwework">
  <div class="woman" role="img" aria-label="Photo of a smiling businesswoman holding a folder"></div>
  <div class="copy">
    <h2>How we Work</h2>
    <p>We start with a short call to learn about your business and the tasks you want off your plate. Then we match you with an assistant who suits your needs and working style.</p>
    <p>Send requests by email or phone whenever you like. Your assistant completes each task, keeps you updated and learns your preferences over time.</p>
    <a class="btn btn-solid">Read More</a>
  </div>
</section>

<section class="consult">
  <h2>Request a Consultation</h2>
  <p>Mauris vel iacus vitae felis vestibulum volutpat eu imperdiet sociis natoque penatibus</p>
  <a class="btn">Get Started</a>
</section>

<footer class="footer">
  <div class="wrap">
    <div class="cols">
      <div class="col"><h4>Company</h4><ul><li>About Us</li><li>How it Works</li><li>Prices</li><li>Blog</li><li>Testimonials</li></ul></div>
      <div class="col"><h4>Services</h4><ul><li>Virtual Assist</li><li>Admin</li><li>Bookkeeping</li><li>Scheduling</li><li>Research</li></ul></div>
      <div class="col"><h4>Resources</h4><ul><li>Help Centre</li><li>FAQs</li><li>Client Login</li><li>Careers</li></ul></div>
      <div class="col"><h4>Contact Us</h4><ul><li>48 Harbour Lane, Sydney NSW 2000</li><li>Phone: (02) 5550 0184</li><li>Email: hello@calverbrook.com.au</li></ul>
        <div class="social"><span></span><span></span><span></span><span></span></div>
      </div>
    </div>
  </div>
  <div class="copyright">© 2024 Calverbrook. All rights reserved. Terms of Use</div>
</footer>

</body>
</html>
```